International professional tennis coach needs a book cover design

This is my 2nd published book, the first one was a #1 on the best seller. I'm looking for a world class book cover design for this new book. The name of my first book was 5 Baseline Habits to Unlock Your Flow Rhythm, located on Bookvale.com

The title of the new book:

Title: The Craft of Rally Mastery
Subtitle: Developing a Strategic Advantage through Competitive Intelligence

I'm uploading our new CRAFT OF RALLY logo that I'd like for you to use as the centerpiece of the book design along with a 21st century design feel that incorporates what the book topic is below::

--> This book is about building competitive intelligence by using tennis data analytics to develop and expand a player's strategic advantage for match play. <--

The colors we would like to use are Blue, Yellow, and Green. These shades of these colors should be bold! (You will see the bold color examples of blues, yellows, and greens that I'm talking about in the logos that are attached here, especially the colors for my Racket GridDrill App logo.

I will upload the Racket GridDrill logo which should go somewhere on the back cover design (small size maybe in the bottom corner).

This book is revolutionary to the standard way of teaching tennis, it is based on a decade of recording and gathering tennis data analytics and then we created on-court practice games to develop better decision making in players for the competitive edge.

My websites are www.elevatedrillzone.com and www.craftofrallymastery.com

```html
<!DOCTYPE html>
<html lang="en">
<head>
<meta charset="utf-8">
<title>The Craft of Rally Mastery – Book Cover</title>
<link href="https://fonts.googleapis.com/css2?family=Allura&family=Montserrat:wght@400;500&family=Oswald:wght@500&family=Playfair+Display:wght@400;700;900&display=swap" rel="stylesheet">
<style>
  :root {
    --green-dark: #2f7d2c;
    --green-light: #8cc63f;
    --blue: #1f6fff;
    --yellow: #fcc81e;
    --ink: #2b2b2b;
    --paper: #ffffff;
    --backdrop: #e9eaec;
  }
  * { box-sizing: border-box; margin: 0; padding: 0; }
  html, body { width: 1200px; height: 924px; overflow: hidden; }
  body {
    background: var(--backdrop);
    display: flex; align-items: center; justify-content: center;
    font-family: "Montserrat", sans-serif;
  }
  .book-jacket {
    display: flex; height: 780px;
    box-shadow: 0 10px 30px rgba(0,0,0,.12);
  }
  .cover { width: 520px; height: 100%; background: var(--paper); position: relative; }

  /* ---------- back cover ---------- */
  .back-cover { padding: 58px 36px 30px 40px; }
  .back-heading { display: flex; align-items: baseline; justify-content: center; gap: 8px; }
  .script { font-family: "Allura", cursive; color: var(--green-light); }
  .back-heading .script { font-size: 30px; }
  .back-heading .title { font-family: "Playfair Display", serif; font-weight: 900; color: var(--green-dark); font-size: 33px; letter-spacing: -0.5px; }
  .blurb { margin-top: 28px; font-size: 9.4px; line-height: 1.5; color: var(--ink); text-align: justify; }
  .blurb p + p { margin-top: 3px; }
  .rule { height: 1px; width: 260px; margin: 14px auto 12px; background: linear-gradient(90deg, transparent, var(--green-light), transparent); }
  .author-name { font-family: "Playfair Display", serif; font-weight: 900; color: var(--green-dark); font-size: 25px; text-align: center; letter-spacing: .5px; }
  .author { display: flex; gap: 12px; margin-top: 8px; }
  .author-photo { flex: 0 0 86px; height: 96px; border: 1px solid #3a5a8a; }
  .photo-one { background: linear-gradient(160deg, #5d6b4f, #8a8f86 55%, #2a2d33); }
  .photo-two { background: linear-gradient(160deg, #7fa5c9, #9a8b6a 55%, #2f3b55); }
  .author-bio { font-size: 9.2px; line-height: 1.42; color: var(--ink); text-align: justify; }
  .app-mark { position: absolute; left: 40px; bottom: 34px; display: flex; align-items: center; gap: 6px; }
  .app-mark .dot { width: 14px; height: 14px; border-radius: 50%; background: var(--blue); }
  .app-mark span { font-family: "Montserrat", sans-serif; font-weight: 500; font-size: 10px; color: var(--green-dark); }

  /* ---------- spine ---------- */
  .spine {
    width: 52px; height: 100%; background: var(--paper);
    border-left: 1px solid #e2e2e2; border-right: 1px solid #e2e2e2;
    display: flex; flex-direction: column; align-items: center; padding: 40px 0 30px;
    writing-mode: vertical-rl;
  }
  .spine .script { font-size: 20px; }
  .spine .title { font-family: "Playfair Display", serif; font-weight: 900; color: var(--green-dark); font-size: 24px; margin-top: 8px; }
  .spine .mark { width: 16px; height: 16px; border-radius: 50%; background: var(--blue); margin: 30px 0; }
  .spine .authors { font-family: "Oswald", sans-serif; font-weight: 500; color: var(--green-dark); font-size: 16px; }

  /* ---------- front cover ---------- */
  .front-cover { padding-top: 80px; text-align: center; }
  .front-cover .script { font-size: 62px; line-height: 1; }
  .front-title { font-family: "Playfair Display", serif; font-weight: 900; color: var(--green-dark); font-size: 82px; line-height: .98; letter-spacing: -1px; margin-top: 4px; }
  .brand-mark { margin: 70px auto 0; display: flex; align-items: center; justify-content: center; gap: 12px; height: 150px; }
  .brand-mark .dot { width: 26px; height: 26px; border-radius: 50%; background: var(--blue); }
  .brand-mark span { font-family: "Playfair Display", serif; font-weight: 700; font-size: 30px; color: var(--blue); letter-spacing: 1px; }
  .subtitle-block { margin: 50px auto 0; width: 380px; }
  .subtitle-block .rule { width: 320px; margin: 0 auto 10px; }
  .subtitle { font-family: "Playfair Display", serif; font-size: 23px; line-height: 1.15; color: var(--ink); }
  .subtitle-block .rule.bottom { margin: 12px auto 0; }
  .front-authors { position: absolute; left: 0; right: 0; bottom: 70px; font-family: "Oswald", sans-serif; font-weight: 500; font-size: 32px; color: var(--green-dark); }
</style>
</head>
<body>
  <div class="book-jacket">

    <section class="cover back-cover">
      <h2 class="back-heading"><span class="script">The Craft of</span><span class="title">RALLY MASTERY</span></h2>
      <div class="blurb">
        <p>A practical guide on how to win more matches by becoming a more efficient and effective competitor.</p>
        <p>As a tennis player you have the ability to play better matches and win more of them. The Craft of Rally Mastery gives you a system to improve. We start with the individual game of the set itself. Our system examines your physical and mental progression, enabling you to upgrade your movement and performance from shot to shot and point to point. Our system seamlessly integrates the technical (physical) aspects with the tactical (mental/emotional) components, providing a comprehensive approach to elevate this performance. We aim to give you much more than how to hit great shots. Irrespective of your current skill level, we will provide you with a detailed strategic and tactical plan to enhance your performance, leading to improved results and increased success in your matches.</p>
        <p>The Craft of Rally Mastery emphasizes the importance of shifting focus from oneself to the opponent, encouraging players to analyze and understand their adversaries. By bringing the opponent back to the forefront of their thinking, the player creates the best possible context in which to improve as a competitor. In this book, we present a groundbreaking approach to tennis data analytics that seamlessly integrates match performance with practice sessions, and vice versa.</p>
      </div>

      <div class="rule"></div>
      <h3 class="author-name">CORWIN HALVEY</h3>
      <div class="author">
        <div class="author-photo photo-one" role="img" aria-label="Portrait photo of author Corwin Halvey in a white cap on court"></div>
        <p class="author-bio">Corwin Halvey is regarded as one of the leading strategy and tactical coaches in the world today. He is the Creator of Racket GridDrill, the world's first Tennis Tracking App that maps and charts match play based on the rally length of a point. Corwin is a Best Selling Author of the book "5 Baseline Habits to Unlock Your Flow Rhythm" and the Co-Founder of The Craft of Rally Mastery promoting coach, player, and parent development. He is often sought after by coaches around the world to design the practice court in a way that revolutionizes a player's mindset to successfully negotiate the pressures of competitive match play.</p>
      </div>

      <div class="rule"></div>
      <h3 class="author-name">REED MALLORAN</h3>
      <div class="author">
        <div class="author-photo photo-two" role="img" aria-label="Portrait photo of author Reed Malloran outdoors"></div>
        <p class="author-bio">Reed Malloran is a writer and tennis coach. He is a Co-Founder at The Craft of Rally Mastery and has been working to create a theoretical framework for tennis players of all levels to improve. Reed studies the forces that act on the player during a tennis match (both internal and external) and works with players to meet the challenge these forces represent. He runs online and on court programs designed specifically to improve a player's Competitive Intelligence.</p>
      </div>

      <div class="app-mark"><i class="dot"></i><span>Racket GridDrill</span></div>
    </section>

    <aside class="spine">
      <span class="script">The Craft of</span>
      <span class="title">RALLY MASTERY</span>
      <i class="mark"></i>
      <span class="authors">CORWIN HALVEY &amp; REED MALLORAN</span>
    </aside>

    <section class="cover front-cover">
      <div class="script">The Craft of</div>
      <h1 class="front-title">RALLY<br>MASTERY</h1>
      <div class="brand-mark"><i class="dot"></i><span>CRAFT OF RALLY</span></div>
      <div class="subtitle-block">
        <div class="rule"></div>
        <p class="subtitle">Developing a Strategic Advantage through Competitive Intelligence</p>
        <div class="rule bottom"></div>
      </div>
      <p class="front-authors">CORWIN HALVEY &amp; REED MALLORAN</p>
    </section>

  </div>
</body>
</html>
```